we are an outdoor outlet in a country club that has a variety of outlets. The Club is called Meadowlark and is located in Cairo, Egypt. This garden menu will include cuisines from the Mediterranean, Asia and Texmex. we need a menu that is colorful and would fit an A3 size, back and front are to be used. Attached is the old menu currently in use (Garden Menu 2012.pdf is just for reference) and the new menu text for you to use is under the name Garden Menu Fall 2013
thank you.
Updates
Logo files have been uploaded for this project
Industry/Entity Type
Club
Look and feel
Each slider illustrates characteristics of the customer's brand and the style your logo design should communicate.

```html
<!DOCTYPE html>
<html lang="en">
<head>
<meta charset="utf-8">
<title>Meadowlark Country Club – Garden Menu</title>
<link href="https://fonts.googleapis.com/css2?family=EB+Garamond:wght@400;500&display=swap" rel="stylesheet">
<style>
  :root{
    --paper:#f6eed8;
    --gutter:#ffffff;
    --ink:#3b2d25;
    --muted:#5a4a40;
    --accent:#e0683a;
    --leaf:#b9cb3a;
    --leaf-dark:#8fa82a;
    --cactus:#6e9a3c;
  }
  *{box-sizing:border-box;margin:0;padding:0}
  html,body{width:1200px;height:841px;overflow:hidden;background:var(--gutter)}
  body{font-family:"EB Garamond",Garamond,Georgia,serif;color:var(--ink)}
  .canvas{position:relative;width:1200px;height:841px}
  .page{position:absolute;top:0;width:594px;height:841px;background:var(--paper);overflow:hidden}
  .page--front{left:0}
  .page--back{left:606px}

  .col{position:absolute;z-index:2}
  .section-title{font-size:24px;font-weight:400;color:var(--accent);line-height:1.05}
  .section-note{font-size:7px;color:var(--muted);margin-top:1px}
  .corner-title{font-size:26px;font-weight:400;color:var(--ink);text-decoration:underline;text-underline-offset:4px;text-decoration-thickness:1.5px;line-height:1.15}

  .menu-list{list-style:none;margin-top:var(--top,12px)}
  .item{margin-bottom:var(--gap,10px)}
  .item-row{display:flex;justify-content:space-between;align-items:baseline}
  .item-name{font-size:12.5px;line-height:14px}
  .item-name small{font-size:7.5px}
  .price{font-size:12px;line-height:14px;white-space:nowrap}
  .item-desc{font-size:7px;line-height:8px;color:var(--muted);max-width:210px}
  .detail{font-size:7px;line-height:8px;color:var(--muted);margin-top:8px;max-width:260px}

  .brand{position:absolute;z-index:2;text-align:center;color:var(--ink)}
  .brand-name{font-size:40px;font-weight:400;letter-spacing:1px;line-height:1;display:block}
  .brand-sub{font-size:15px;letter-spacing:5px;display:block;margin-top:2px}
  .brand-dot{display:inline-block;width:34px;height:34px;border-radius:50%;background:var(--leaf);margin-bottom:10px}

  .art{position:absolute;z-index:1}
  .shrubs{left:0;bottom:0;width:594px;height:70px;background:linear-gradient(180deg,#cdd96a 0%,var(--leaf) 60%);border-radius:60% 60% 0 0/100% 100% 0 0;opacity:.9}
  .sprig{width:58px;height:16px;background:var(--leaf-dark);border-radius:50%;opacity:.8}
  .bamboo{top:0;height:86px;background:linear-gradient(90deg,#c3d45a,#a9c03a)}
  .cactus{width:34px;height:58px;background:linear-gradient(180deg,#86b04a,var(--cactus));border-radius:14px 14px 4px 4px}

  .footnote{position:absolute;z-index:2;font-size:10px;color:var(--muted)}
  .contact{position:absolute;z-index:2;text-align:center;font-size:14px;line-height:19px;color:var(--ink)}
</style>
</head>
<body>
<main class="canvas">

  <section class="page page--front">
    <div class="art shrubs" role="img" aria-label="Illustrated green shrubs along the page foot"></div>

    <div class="brand" style="left:40px;top:52px;width:230px">
      <span class="brand-dot"></span>
      <span class="brand-name">Meadowlark</span>
      <span class="brand-sub">country club</span>
    </div>

    <div class="art sprig" style="left:32px;top:212px" role="img" aria-label="Leaf and acorn sprig ornament"></div>
    <div class="art sprig" style="left:206px;top:212px" role="img" aria-label="Leaf and acorn sprig ornament"></div>
    <h1 class="col corner-title" style="left:64px;top:180px;width:180px;text-align:center">Mediterranean<br>Corner</h1>

    <div class="col" style="left:20px;top:266px;width:262px">
      <h2 class="section-title">Pizza &amp; Pasta:</h2>
      <ul class="menu-list" style="--top:14px">
        <li class="item">
          <div class="item-row"><span class="item-name">Pizza Margarita</span><span class="price">L.E X.xx</span></div>
          <p class="item-desc">(Choose your toppings) Create your own pasta</p>
          <p class="detail">Type: Spaghetti, Tagliatelle, Penne</p>
          <p class="detail">Sauces: Napolitana, Bolognese, Alfredo</p>
          <p class="detail">Toppings: Bell peppers, olives, tomato, onion Mushroom, chicken, tuna, pepperoni Smoked salmon, shrimps Lasagna</p>
        </li>
      </ul>
    </div>

    <div class="col" style="left:20px;top:398px;width:262px">
      <h2 class="section-title">Sandwiches:</h2>
      <p class="section-note">(Served with French fries or a garden salad)</p>
      <ul class="menu-list" style="--top:10px;--gap:8px">
        <li class="item"><div class="item-row"><span class="item-name">Beef or chicken shawerma</span><span class="price">L.E X.xx</span></div></li>
        <li class="item"><div class="item-row"><span class="item-name">Grilled kofta</span><span class="price">L.E X.xx</span></div></li>
        <li class="item"><div class="item-row"><span class="item-name">Greek lamb gyro</span><span class="price">L.E X.xx</span></div><p class="item-desc">in pita bread with Tzatziki</p></li>
        <li class="item"><div class="item-row"><span class="item-name">Club sandwich</span><span class="price">L.E X.xx</span></div><p class="item-desc">with smoked beef, turkey, egg</p></li>
      </ul>
    </div>

    <div class="col" style="left:20px;top:551px;width:262px">
      <h2 class="section-title">Main Courses:</h2>
      <ul class="menu-list" style="--top:10px;--gap:9px">
        <li class="item"><div class="item-row"><span class="item-name">Veal parmeggiana</span><span class="price">L.E X.xx</span></div><p class="item-desc">Breaded veal escalope topped with melted cheese and tomato sauce served with Spaghetti</p></li>
        <li class="item"><div class="item-row"><span class="item-name">Chicken a la francaise</span><span class="price">L.E X.xx</span></div><p class="item-desc">Pan fried chicken breast in a mushroom cream sauce with vegetables white rice</p></li>
        <li class="item"><div class="item-row"><span class="item-name">Grilled salmon</span><span class="price">L.E X.xx</span></div><p class="item-desc">Salmon steak charcoal grilled with avocado tomato relish and creamy mushroom risotto</p></li>
        <li class="item"><div class="item-row"><span class="item-name">Moroccan chicken</span><span class="price">L.E X.xx</span></div><p class="item-desc">Chicken cubes simmered with spices and olives served with tomato rice</p></li>
        <li class="item"><div class="item-row"><span class="item-name">Filet</span><span class="price">L.E X.xx</span></div><p class="item-desc">Tender filet grilled to your liking served with mashed potato and creamed spinach</p><p class="detail">Choice of sauces: Brown mushrooms, Green Peppercorn, Gorgonzola</p></li>
      </ul>
    </div>

    <div class="col" style="left:315px;top:36px;width:260px">
      <h2 class="section-title">Soup:</h2>
      <ul class="menu-list" style="--top:10px;--gap:9px">
        <li class="item"><div class="item-row"><span class="item-name">Tomato basil</span><span class="price">L.E X.xx</span></div><p class="item-desc">Simmered tomato soup finished with fresh basil and cream</p></li>
        <li class="item"><div class="item-row"><span class="item-name">Chicken cream</span><span class="price">L.E X.xx</span></div><p class="item-desc">Chicken broth with roasted chicken cubes, pine nuts, and cream</p></li>
        <li class="item"><div class="item-row"><span class="item-name">Moroccan harira</span><span class="price">L.E X.xx</span></div><p class="item-desc">Vegetable broth with fresh tomato, chickpeas, lentil, cilantro and diced lamb</p></li>
      </ul>
    </div>

    <div class="col" style="left:315px;top:178px;width:260px">
      <h2 class="section-title">Appetizers:</h2>
      <ul class="menu-list" style="--top:12px;--gap:9.5px">
        <li class="item"><div class="item-row"><span class="item-name">Salmon tartare</span><span class="price">L.E X.xx</span></div><p class="item-desc">seasoned with lemon juice, garlic, and crushed black pepper</p></li>
        <li class="item"><div class="item-row"><span class="item-name">Roasted eggplant rolls</span><span class="price">L.E X.xx</span></div><p class="item-desc">with herbed ricotta cheese and pine nuts</p></li>
        <li class="item"><div class="item-row"><span class="item-name">Falafel in mini pita</span><span class="price">L.E X.xx</span></div><p class="item-desc">served with tehina and oriental salsa</p></li>
        <li class="item"><div class="item-row"><span class="item-name">Mankousha</span><span class="price">L.E X.xx</span></div><p class="item-desc">with thyme and olive oil</p></li>
        <li class="item"><div class="item-row"><span class="item-name">Fried kobeba</span><span class="price">L.E X.xx</span></div><p class="item-desc">with minced meat, spices, and pine nuts</p></li>
        <li class="item"><div class="item-row"><span class="item-name">Fried calamari a la Romana</span><span class="price">L.E X.xx</span></div><p class="item-desc">served with aioli</p></li>
        <li class="item"><div class="item-row"><span class="item-name">Samboussek</span><span class="price">L.E X.xx</span></div><p class="item-desc">with herbed white cheese and mint</p></li>
        <li class="item"><div class="item-row"><span class="item-name">Oriental sausage</span><span class="price">L.E X.xx</span></div><p class="item-desc">sautéed with garlic and onion</p></li>
        <li class="item"><div class="item-row"><span class="item-name">Mini vine</span><span class="price">L.E X.xx</span></div><p class="item-desc">leaves with a yoghurt dip</p></li>
        <li class="item"><div class="item-row"><span class="item-name">Fatouch</span><span class="price">L.E X.xx</span></div><p class="item-desc">with a pomegranate syrup dressing</p></li>
        <li class="item"><div class="item-row"><span class="item-name">Hummus</span><span class="price">L.E X.xx</span></div><p class="item-desc">seasoned with lemon juice, garlic, and olive oil</p></li>
        <li class="item"><div class="item-row"><span class="item-name">White cheese</span><span class="price">L.E X.xx</span></div><p class="item-desc">with diced tomato, thyme, and olive oil</p></li>
        <li class="item"><div class="item-row"><span class="item-name">Tehina</span><span class="price">L.E X.xx</span></div><p class="item-desc">seasoned with cumin, lemon juice, and garlic</p></li>
      </ul>
    </div>

    <div class="col" style="left:315px;top:632px;width:260px">
      <h2 class="section-title">Salads:</h2>
      <ul class="menu-list" style="--top:10px;--gap:8px">
        <li class="item"><div class="item-row"><span class="item-name">Caprese</span><span class="price">L.E X.xx</span></div><p class="item-desc">Buffalo mozzarella and sliced tomato with a balsamic vinaigrette</p></li>
        <li class="item"><div class="item-row"><span class="item-name">Rocket apple</span><span class="price">L.E X.xx</span></div><p class="item-desc">Rocket leaves with gorgonzola, croutons, and strawberry vinaigrette</p></li>
        <li class="item"><div class="item-row"><span class="item-name">French Riviera Nicoise</span><span class="price">L.E X.xx</span></div><p class="item-desc">Lettuce, egg, tomato, tuna, olives, onion, celery, radish, bell pepper in a French vinaigrette</p></li>
        <li class="item"><div class="item-row"><span class="item-name">Folle</span><span class="price">L.E X.xx</span></div><p class="item-desc">Mixed greens with crab sticks, mushroom, corn, cherry tomato in a mango vinaigrette</p></li>
      </ul>
    </div>
  </section>

  <section class="page page--back">
    <div class="art shrubs" role="img" aria-label="Illustrated green shrubs along the page foot"></div>
    <div class="art bamboo" style="left:20px;width:68px" role="img" aria-label="Illustrated bamboo stalks"></div>
    <div class="art bamboo" style="left:230px;width:60px" role="img" aria-label="Illustrated bamboo stalks"></div>

    <h1 class="col corner-title" style="left:75px;top:30px">Asian Corner</h1>

    <div class="col" style="left:20px;top:76px;width:260px">
      <h2 class="section-title">Salads &amp; Appetizers:</h2>
      <ul class="menu-list" style="--top:12px;--gap:9px">
        <li class="item"><div class="item-row"><span class="item-name">Chicken wasabi salad</span><span class="price">L.E X.xx</span></div><p class="item-desc">Diced chicken with a mayo wasabi dressing on top of shredded lettuce</p></li>
        <li class="item"><div class="item-row"><span class="item-name">Chicken sesame noodle salad</span><span class="price">L.E X.xx</span></div><p class="item-desc">Sesame crusted chicken with glass noodles tossed with sweet chili, soy sauce, and lemongrass</p></li>
        <li class="item"><div class="item-row"><span class="item-name">Spring rolls</span><span class="price">L.E X.xx</span></div><p class="item-desc">Vegetable spring rolls served with house made sweet and sour dip</p></li>
        <li class="item"><div class="item-row"><span class="item-name">Indian samosa</span><span class="price">L.E X.xx</span></div><p class="item-desc">Fried dough parcels filled with vegetables and spices</p></li>
      </ul>
    </div>

    <div class="col" style="left:20px;top:258px;width:260px">
      <h2 class="section-title">Main Courses:</h2>
      <ul class="menu-list" style="--top:12px;--gap:12px">
        <li class="item"><div class="item-row"><span class="item-name">Murgh chicken makhni</span><span class="price">L.E X.xx</span></div><p class="item-desc">Chicken cubes in a rich creamy tomato sauce seasoned with garam masala</p><p class="item-desc">Choice of side: vegetable korma or curd</p></li>
        <li class="item"><div class="item-row"><span class="item-name">Chicken tandoori</span><span class="price">L.E X.xx</span></div><p class="item-desc">Grilled chicken cubes with tandoori spices served with basmati rice</p></li>
        <li class="item"><div class="item-row"><span class="item-name">Thai coconut curry shrimp</span><span class="price">L.E X.xx</span></div><p class="item-desc">Sautéed shrimp tossed with curry and coconut milk served with jasmine rice</p></li>
        <li class="item"><div class="item-row"><span class="item-name">Mongolian beef</span><span class="price">L.E X.xx</span></div><p class="item-desc">Soy marinated beef with oyster sauce and vegetables served with egg noodles</p></li>
      </ul>
    </div>

    <div class="art cactus" style="left:46px;top:510px" role="img" aria-label="Illustrated cactus"></div>
    <div class="art cactus" style="left:226px;top:510px" role="img" aria-label="Illustrated cactus"></div>
    <h1 class="col corner-title" style="left:102px;top:518px">Tex Mex</h1>

    <div class="col" style="left:20px;top:566px;width:260px">
      <h2 class="section-title">Salads &amp; Appetizers:</h2>
      <ul class="menu-list" style="--top:12px;--gap:9px">
        <li class="item"><div class="item-row"><span class="item-name">Caesar salad</span><span class="price">L.E X.xx</span></div><p class="item-desc">Iceberg lettuce with Caesar dressing with grated Parmesan cheese and croutons</p></li>
        <li class="item"><div class="item-row"><span class="item-name">Taco salad 42</span><span class="price">L.E X.xx</span></div><p class="item-desc">Chicken breast, beans, sour cream, guacamole, tomato, corn, lettuce, olives, chives, vinaigrette</p></li>
        <li class="item"><div class="item-row"><span class="item-name">Nachos</span><span class="price">L.E X.xx</span></div><p class="item-desc">topped with chili, melted cheese, beans</p></li>
        <li class="item"><div class="item-row"><span class="item-name">Chicken Quesadilla</span><span class="price">L.E X.xx</span></div><p class="item-desc">served with guacamole, salsa, and sour cream</p></li>
      </ul>
    </div>

    <p class="footnote" style="left:46px;top:802px">Prices are subjects to 12% service Charge and 10% Sales Tax</p>

    <div class="col" style="left:315px;top:36px;width:260px">
      <h2 class="section-title">Main Courses &amp;<br>Sandwiches:</h2>
      <ul class="menu-list" style="--top:12px;--gap:9px">
        <li class="item"><div class="item-row"><span class="item-name">Cheese burger</span><span class="price">L.E X.xx</span></div><p class="item-desc">House made lean beef burger topped with cheddar cheese</p></li>
        <li class="item"><div class="item-row"><span class="item-name">Mushroom burger</span><span class="price">L.E X.xx</span></div><p class="item-desc">Beef burger with sautéed mushrooms, caramelized onion, and provolone cheese</p></li>
        <li class="item"><div class="item-row"><span class="item-name">Crispy chicken wrap</span><span class="price">L.E X.xx</span></div><p class="item-desc">Crisp fried chicken wrap with a ranch dressing</p></li>
        <li class="item"><div class="item-row"><span class="item-name">Fajita <small>(Chicken, Beef, Combo)</small></span><span class="price">L.E X.xx</span></div><p class="item-desc">pan seared meat or chicken with onion and bell pepper served with sour cream, guacamole, salsa</p></li>
      </ul>
    </div>

    <div class="col" style="left:315px;top:250px;width:260px">
      <h2 class="section-title">Desserts:</h2>
      <ul class="menu-list" style="--top:14px;--gap:8.5px">
        <li class="item"><div class="item-row"><span class="item-name">Mix berries cheesecake</span><span class="price">L.E X.xx</span></div></li>
        <li class="item"><div class="item-row"><span class="item-name">Crème brulee</span><span class="price">L.E X.xx</span></div></li>
        <li class="item"><div class="item-row"><span class="item-name">Chocolate caramel cake</span><span class="price"></span></div></li>
        <li class="item"><div class="item-row"><span class="item-name">Warm chocolate fondant</span><span class="price">L.E X.xx</span></div></li>
        <li class="item"><div class="item-row"><span class="item-name">Baked apple tart tatin</span><span class="price">L.E X.xx</span></div></li>
        <li class="item"><div class="item-row"><span class="item-name">Tiramisu</span><span class="price">L.E X.xx</span></div></li>
        <li class="item"><div class="item-row"><span class="item-name">Pumpkin pie flan</span><span class="price">L.E X.xx</span></div></li>
        <li class="item"><div class="item-row"><span class="item-name">Mixed berries granola yoghurt</span><span class="price">L.E X.xx</span></div></li>
        <li class="item"><div class="item-row"><span class="item-name">Vanilla ice cream</span><span class="price">L.E X.xx</span></div><p class="item-desc">profiterole with dark and white chocolate sauce</p></li>
        <li class="item"><div class="item-row"><span class="item-name">Caramelized banana</span><span class="price">L.E X.xx</span></div><p class="item-desc">with Deep Fried Ice Cream</p></li>
        <li class="item"><div class="item-row"><span class="item-name">Baklava</span><span class="price">L.E X.xx</span></div><p class="item-desc">with Nuts and Sugar Syrup</p></li>
        <li class="item"><div class="item-row"><span class="item-name">Shot glass sampler</span><span class="price">L.E X.xx</span></div><p class="item-desc">Tiramisu, Chocolate Crisp Mousse, Pear with Sabayon</p></li>
        <li class="item"><div class="item-row"><span class="item-name">Ice cream</span><span class="price">L.E X.xx</span></div><p class="item-desc">by Scoop</p></li>
      </ul>
    </div>

    <div class="brand" style="left:340px;top:662px;width:210px">
      <span class="brand-dot"></span>
      <span class="brand-name" style="font-size:34px">Meadowlark</span>
      <span class="brand-sub" style="font-size:13px">country club</span>
    </div>
    <div class="contact" style="left:340px;top:774px;width:210px">
      <p>Contact us: Cairo, Egypt</p>
      <p>Tel: (0321) 5550 48120</p>
    </div>
  </section>

</main>
</body>
</html>
```